zorvan lumet website design

An IT support and IT Security Company - just use dummy text for now for the design. Examples of sites we like the looks and feel of but need it more professional feel are like: www.kelbrovault.uk.com , www.pravok.co.uk, www.quenthardy.com/professional/, www.vur.com, www.melvish.com,

Best to message me if you have any questions

Target Market(s)

small to medium UK based companies that require IT support services

Industry/Entity Type

It Company

Contact Information for Business Card

use dummy name, telephone and email for now, will provide details later.

Logo Text

zorvan lumet (and then below the logo it should say "your IT, networks and security partner")

Coding

Coded - Design and coding required

Number of Pages Required

5+ page

Colors

Designer to choose colors to be used in the design.

Requirements
Must have
• must be professional, yet simple and clear that this is a serious IT support and IT security company.
Nice to have
• 1)The website homepage must have professional quality pictures of IT support or London city skyline or any picture that projects friendly business partners, professionalism and ready to serve.
• 2) Home page needs to include tabs for following pages 'Services' , 'About Us' , 'Contact Us' 'Home'
• 3) Website built customised using wordpress is ideal and easy for us to manage.
• more room for boxed options from homepage (with pic or image in background)
Should not have
• no checkout trolleys or payment options.

```html
<!DOCTYPE html>
<html lang="en">
<head>
<meta charset="utf-8">
<title>zorvan lumet — IT support and IT security</title>
<link rel="stylesheet" href="https://fonts.googleapis.com/css2?family=Questrial&family=Mulish:wght@400;600&display=swap">
<style>
  :root{
    --navy:#302e63;
    --navy-dark:#26244f;
    --ink:#2b2a5c;
    --grey-head:#8c8c92;
    --body-text:#8f8f96;
    --service-text:#5c5c63;
    --white:#ffffff;
    --hero-top:#2c3440;
    --hero-mid:#6b5a45;
    --hero-low:#2a2620;
    --band-a:#3a3430;
    --band-b:#5a4e44;
  }
  *{box-sizing:border-box;margin:0;padding:0}
  html,body{width:694px;height:1200px;overflow:hidden;background:var(--white)}
  body{font-family:"Mulish",sans-serif;color:var(--body-text);position:relative}
  .heading{font-family:"Questrial",sans-serif;font-weight:400}

  /* hero */
  .hero{position:absolute;left:0;top:0;width:694px;height:392px;
    background:linear-gradient(180deg,var(--hero-top) 0%,#4e4a48 35%,var(--hero-mid) 55%,#4a3b2c 75%,var(--hero-low) 100%)}
  .hero-photo{position:absolute;inset:0}
  .brand{position:absolute;display:flex;align-items:center;gap:7px;color:var(--white);font-family:"Questrial",sans-serif;font-size:24px;letter-spacing:.3px;white-space:nowrap}
  .brand-mark{width:14px;height:14px;background:#d8d8d8}
  .hero .brand{left:45px;top:20px}
  .nav{position:absolute;top:28px;left:364px;width:300px;height:20px}
  .nav a{position:absolute;top:0;font-size:8px;color:var(--white);text-decoration:none;letter-spacing:.3px;white-space:nowrap}
  .nav a:nth-child(1){left:0}
  .nav a:nth-child(2){left:76px}
  .nav a:nth-child(3){left:156px}
  .nav a:nth-child(4){left:246px}
  .nav .active::after{content:"";position:absolute;left:-5px;top:14px;width:34px;border-top:2px dotted var(--white)}
  .hero-title{position:absolute;top:118px;left:0;width:694px;text-align:center;color:var(--white);font-size:49px;letter-spacing:.5px}
  .hero-text{position:absolute;top:188px;left:0;width:694px;text-align:center;color:var(--white);font-size:13px;line-height:18px}
  .btn-light{position:absolute;left:273px;top:236px;width:148px;height:36px;background:var(--white);color:#111;font-size:15px;font-weight:600;display:flex;align-items:center;justify-content:center;letter-spacing:.3px}

  /* welcome */
  .welcome{position:absolute;top:392px;left:0;width:694px;height:223px;background:var(--white)}
  .welcome-photo{position:absolute;left:40px;top:30px;width:220px;height:193px;background:linear-gradient(160deg,#d9d9dc,#bfc0c4 60%,#cfa68a)}
  .welcome-title{position:absolute;left:278px;top:28px;font-size:23px;color:var(--grey-head);white-space:nowrap}
  .welcome-title b{font-weight:400;color:var(--ink)}
  .welcome-copy{position:absolute;left:278px;top:67px;width:372px;font-size:8.6px;line-height:14.5px}
  .welcome-copy p+p{margin-top:7px}
  .btn{position:absolute;height:32px;width:96px;background:var(--navy);color:var(--white);font-size:11.5px;display:flex;align-items:center;justify-content:center;gap:8px;border-bottom:2px solid var(--navy-dark);white-space:nowrap}
  .welcome .btn{left:277px;top:157px}

  /* services */
  .services{position:absolute;top:615px;left:0;width:694px;height:327px;background:linear-gradient(120deg,#f3f3f3,#e9e9e9 50%,#f2f2f2)}
  .service{position:absolute;top:0;width:240px;height:327px;text-align:center}
  .service.support{left:81px}
  .service.security{left:371px}
  .service-title{position:absolute;top:31px;left:0;width:100%;font-size:17px;color:var(--ink)}
  .service-title span{color:var(--grey-head)}
  .service-art{position:absolute;top:74px;left:60px;width:120px;height:120px;border-radius:50%}
  .support .service-art{background:radial-gradient(circle,#2f5a78 0%,#3c6f8e 35%,rgba(239,239,239,0) 70%)}
  .security .service-art{background:radial-gradient(circle,#244e6a 0%,#4a97b4 40%,rgba(239,239,239,0) 72%)}
  .service-text{position:absolute;top:222px;left:8px;width:224px;font-size:9px;line-height:13px;color:var(--service-text)}
  .service .btn{top:265px;left:72px}
  .divider{position:absolute;left:346px;top:63px;height:208px;border-left:1px dotted #8a8a8a}
  .amp{position:absolute;left:325px;top:134px;width:42px;height:42px;border-radius:50%;background:var(--white);border:4px solid #e6e6e6;color:var(--ink);font-size:16px;display:flex;align-items:center;justify-content:center;font-family:"Questrial",sans-serif}

  /* clients band */
  .clients{position:absolute;top:942px;left:0;width:694px;height:166px;background:linear-gradient(100deg,var(--band-a),var(--band-b) 55%,#3b322b)}
  .clients-title{position:absolute;top:28px;left:0;width:100%;text-align:center;color:var(--white);font-size:25px}
  .clients-text{position:absolute;top:67px;left:80px;width:534px;text-align:center;color:var(--white);font-size:11px;line-height:15px}
  .clients .btn{top:104px;left:291px;width:112px}

  /* footer */
  .footer{position:absolute;top:1108px;left:0;width:694px;height:92px;background:var(--navy)}
  .footer .brand{left:45px;top:14px;font-size:20px}
  .phone{position:absolute;left:290px;top:15px;display:flex;align-items:center;gap:9px;color:var(--white);font-size:13.5px}
  .phone-icon{width:24px;height:24px;border-radius:50%;background:var(--white);display:flex;align-items:center;justify-content:center}
  .social{position:absolute;left:539px;top:15px;display:flex;gap:4px}
  .social span{width:24px;height:24px;border-radius:50%;border:1.5px solid #8b89b0}
  .social span:first-child{background:var(--white);border-color:var(--white)}
  .footer-rule{position:absolute;left:45px;right:45px;top:54px;border-top:1px solid #4e4c7e}
  .copyright{position:absolute;top:68px;left:0;width:100%;text-align:center;font-size:8px;color:#8c8ab0}
  .copyright b{color:var(--white);font-weight:400}
</style>
</head>
<body>
  <header class="hero">
    <div class="hero-photo" role="img" aria-label="City skyline at sunset seen from above"></div>
    <div class="brand"><span class="brand-mark"></span>zorvan lumet</div>
    <nav class="nav">
      <a class="active">HOME</a>
      <a>ABOUT</a>
      <a>SERVICES</a>
      <a>CONTACT</a>
    </nav>
    <h1 class="hero-title heading">Our Clients find Us</h1>
    <p class="hero-text">Lorem Ipsum is simply dummy text of the printing and typesetting industry.<br>Lorem Ipsum has been the industry's standard dummy text..</p>
    <div class="btn-light">EXPLORE MORE</div>
  </header>

  <section class="welcome">
    <div class="welcome-photo" role="img" aria-label="Hands working on a laptop while holding a phone"></div>
    <h2 class="welcome-title heading">Welcome to <b>zorvan lumet</b></h2>
    <div class="welcome-copy">
      <p>Lorem Ipsum is simply dummy text of the printing and typesetting industry. Lorem Ipsum has been the industry's standard dummy text ever since the 1500s, when an unknown printer took a galley of type and scrambled it to make a type specimen book.</p>
      <p>Lorem Ipsum is simply dummy text of the printing and typesetting industry. Lorem Ipsum has been the industry's standard dummy text ever since the 1500.</p>
    </div>
    <div class="btn">READ MORE</div>
  </section>

  <section class="services">
    <div class="service support">
      <h3 class="service-title heading"><span>IT</span> support</h3>
      <div class="service-art" role="img" aria-label="Illustration of a support person inside a gear with tech icons"></div>
      <p class="service-text">Lorem Ipsum is simply dummy text of the printing and typesetting industry. Lorem Ipsum has been the industry's standard dummy text ever since the 1500.</p>
      <div class="btn">READ MORE</div>
    </div>
    <div class="divider"></div>
    <div class="amp">&amp;</div>
    <div class="service security">
      <h3 class="service-title heading"><span>IT</span> Security</h3>
      <div class="service-art" role="img" aria-label="Illustration of a shield in front of computer screens"></div>
      <p class="service-text">Lorem Ipsum is simply dummy text of the printing and typesetting industry. Lorem Ipsum has been the industry's standard dummy text ever since the 1500.</p>
      <div class="btn">READ MORE</div>
    </div>
  </section>

  <section class="clients" role="img" aria-label="Hands typing on a keyboard, darkened background photo">
    <h2 class="clients-title heading">We’ve successfully serviced 25 clients</h2>
    <p class="clients-text">Lorem Ipsum is simply dummy text of the printing and typesetting industry. Lorem Ipsum has been the industry's standard dummy text</p>
    <div class="btn">READ MORE
      <svg width="14" height="13" viewBox="0 0 14 13"><path d="M0 6 L14 0 L11 13 L7 9 L12 2 L5 8 Z" fill="#ffffff"/></svg>
    </div>
  </section>

  <footer class="footer">
    <div class="brand"><span class="brand-mark"></span>zorvan lumet</div>
    <div class="phone">
      <span class="phone-icon"><svg width="13" height="13" viewBox="0 0 24 24"><path d="M6.6 10.8c1.4 2.8 3.8 5.1 6.6 6.6l2.2-2.2c.3-.3.7-.4 1-.2 1.1.4 2.3.6 3.6.6.6 0 1 .4 1 1V20c0 .6-.4 1-1 1C10.6 21 3 13.4 3 4c0-.6.4-1 1-1h3.5c.6 0 1 .4 1 1 0 1.3.2 2.5.6 3.6.1.3 0 .7-.2 1z" fill="none" stroke="#302e63" stroke-width="1.8"/></svg></span>
      123 456 9090
    </div>
    <div class="social" aria-label="Social links"><span></span><span></span><span></span><span></span></div>
    <div class="footer-rule"></div>
    <p class="copyright">© <b>zorvan lumet</b> - 2018. All Right Reserved.</p>
  </footer>
</body>
</html>
```